Falkrin homes and renovations business card design.

Would like some new card designs utilizing my new logo that look professional. I am open to different colors on the logo or utilize the same ones we have. I like the original concept but would like to see some fresh ideas and build on what we have already done.

Target Market(s)

Custom home building industry, Real estate sales, Renovation projects.

Industry/Entity Type

Home Builder

Contact Information for Business Card

Falkrin Homes and Renovations
2871 96th Avenue
Kelvane, Northridge
T2R3W8
Home : 403- 718-4063 Cell: 403- 294-5170

My info is : Dax Falkrin, President and CEO
email: falkrinhomes@maildrop-example.net
Website: falkrinhomes-example.com
websit

Requirements
Must have
• Must Use my new logo design. I am open to different colors on the logo or utilize the same ones in the existing design. I can upload the original logo design if needed.

```html
<!DOCTYPE html>
<html lang="en">
<head>
<meta charset="utf-8">
<title>Falkrin Homes and Renovations – Business Card</title>
<link rel="stylesheet" href="https://fonts.googleapis.com/css2?family=Montserrat:wght@400;500;600&display=swap">
<style>
  :root {
    --page: #e2e3e5;
    --card: #ffffff;
    --charcoal: #3f3f41;
    --gold: #b5832f;
    --yellow: #f7bb1c;
    --ink: #4a4a4c;
    --ink-soft: #6b6b6d;
    --tagline-grey: #a9a9ab;
  }
  * { box-sizing: border-box; margin: 0; padding: 0; }
  html, body { width: 1200px; height: 800px; overflow: hidden; }
  body {
    background: var(--page);
    font-family: "Montserrat", sans-serif;
    position: relative;
  }
  .card {
    position: absolute;
    left: 312px;
    width: 576px;
    height: 320px;
    border-radius: 18px;
    overflow: hidden;
    background: var(--card);
  }
  .card--front { top: 60px; }
  .card--back { top: 420px; }
  .card__art { position: absolute; inset: 0; width: 100%; height: 100%; }

  .holder__name {
    position: absolute; left: 47px; top: 22px;
    font-size: 25px; font-weight: 500; color: var(--ink);
    letter-spacing: 0.3px;
  }
  .holder__title {
    position: absolute; left: 80px; top: 56px;
    font-size: 15px; font-weight: 400; color: var(--ink-soft);
  }
  .contact { position: absolute; left: 45px; top: 0; list-style: none; }
  .contact__item {
    position: absolute; left: 0; display: flex; align-items: center;
    white-space: nowrap;
  }
  .contact__icon {
    width: 27px; height: 27px; border-radius: 50%;
    background: var(--yellow); flex: none;
    display: flex; align-items: center; justify-content: center;
  }
  .contact__icon svg { width: 15px; height: 15px; }
  .contact__text {
    margin-left: 13px; font-size: 13.5px; line-height: 17px; color: var(--ink);
  }
  .contact__item--phone { top: 91px; }
  .contact__item--address { top: 133px; }
  .contact__item--email { top: 178px; }
  .contact__item--web { top: 215px; }

  .brand {
    position: absolute; text-align: center; color: var(--gold);
    font-weight: 600; line-height: 1;
  }
  .brand--small { left: 370px; top: 86px; width: 135px; }
  .brand--small .brand__name { font-size: 23px; letter-spacing: 0.5px; }
  .brand--small .brand__line { font-size: 7px; margin-top: 3px; letter-spacing: 0.3px; }
  .brand--large { left: 70px; top: 172px; width: 270px; }
  .brand--large .brand__name { font-size: 42px; letter-spacing: 0.5px; }
  .brand--large .brand__line { font-size: 14.5px; margin-top: 4px; letter-spacing: 0.4px; color: var(--tagline-grey); }
</style>
</head>
<body>

<section class="card card--front" aria-label="Business card front">
  <svg class="card__art" viewBox="0 0 638 354" preserveAspectRatio="none" aria-hidden="true">
    <path d="M0 303 Q 480 332 638 68 L638 354 L0 354 Z" fill="var(--gold)"/>
    <path d="M0 314 Q 490 340 638 128 L638 354 L0 354 Z" fill="var(--yellow)"/>
    <path d="M0 326 Q 500 334 638 182 L638 354 L0 354 Z" fill="var(--charcoal)"/>
  </svg>

  <h1 class="holder__name">Dax Falkrin</h1>
  <p class="holder__title">President</p>

  <ul class="contact">
    <li class="contact__item contact__item--phone">
      <span class="contact__icon">
        <svg viewBox="0 0 16 16" fill="none" stroke="#fff" stroke-width="1.4"><rect x="4.5" y="1.5" width="7" height="13" rx="1.2"/><line x1="7" y1="12.3" x2="9" y2="12.3"/></svg>
      </span>
      <span class="contact__text">403- 718-4063<br>403- 294-5170</span>
    </li>
    <li class="contact__item contact__item--address">
      <span class="contact__icon">
        <svg viewBox="0 0 16 16"><path d="M8 1.5a4.5 4.5 0 0 0-4.5 4.5c0 3.3 4.5 8.5 4.5 8.5s4.5-5.2 4.5-8.5A4.5 4.5 0 0 0 8 1.5z" fill="#fff"/><circle cx="8" cy="6" r="1.7" fill="var(--yellow)"/></svg>
      </span>
      <span class="contact__text">2871 96th Avenue<br>Kelvane, Northridge</span>
    </li>
    <li class="contact__item contact__item--email">
      <span class="contact__icon">
        <svg viewBox="0 0 16 16" fill="none" stroke="#fff" stroke-width="1.3"><rect x="1.5" y="3.5" width="13" height="9"/><path d="M1.5 3.5 8 9l6.5-5.5M1.5 12.5 6 8M14.5 12.5 10 8"/></svg>
      </span>
      <span class="contact__text">falkrinhomes@maildrop-example.net</span>
    </li>
    <li class="contact__item contact__item--web">
      <span class="contact__icon">
        <svg viewBox="0 0 16 16" fill="none" stroke="#fff" stroke-width="1.2"><circle cx="8" cy="8" r="6.3"/><ellipse cx="8" cy="8" rx="2.8" ry="6.3"/><line x1="1.7" y1="8" x2="14.3" y2="8"/></svg>
      </span>
      <span class="contact__text">www.falkrinhomes-example.com</span>
    </li>
  </ul>

  <div class="brand brand--small">
    <div class="brand__name">FALKRIN</div>
    <div class="brand__line">HOMES AND RENOVATIONS</div>
  </div>
</section>

<section class="card card--back" aria-label="Business card back">
  <svg class="card__art" viewBox="0 0 638 354" preserveAspectRatio="none" aria-hidden="true">
    <path d="M428 212 Q 410 318 282 354 L262 354 Q 392 322 422 238 Z" fill="var(--yellow)"/>
    <path d="M0 0 L447 0 Q 470 150 422 250 Q 370 338 255 354 L0 354 Z" fill="var(--charcoal)"/>
  </svg>
  <div class="brand brand--large">
    <div class="brand__name">FALKRIN</div>
    <div class="brand__line">HOMES AND RENOVATIONS</div>
  </div>
</section>

</body>
</html>
```